Brindovalle Business cards

Dear team, I need to get the design file to suit it to our team. The focus of the business card is the Automotive Market and the design must be in black colour and the logo must be in glossy black. On the front of the card I need to get the following info:

- Name and Surname
- Title
- eMail
- Phone Number
- Skype account
- domain address

```html
<!DOCTYPE html>
<html lang="en">
<head>
<meta charset="utf-8">
<title>Brindovalle Business Card</title>
<link rel="stylesheet" href="https://fonts.googleapis.com/css2?family=Nunito+Sans:wght@400;600;800&display=swap">
<style>
  :root {
    --page-bg: #d9d3cb;
    --card-bg: #f3f2f0;
    --card-edge: #ffffff;
    --band-navy: #0e1640;
    --band-navy-deep: #070b24;
    --brand-red: #e0161d;
    --text-light: #e9ebf3;
    --text-muted: #c9ccd8;
    --text-dark: #23252b;
  }
  * { margin: 0; padding: 0; box-sizing: border-box; }
  html, body { width: 1200px; height: 887px; overflow: hidden; }
  body {
    background: var(--page-bg);
    font-family: "Nunito Sans", Arial, sans-serif;
    position: relative;
  }
  .business-card {
    position: absolute;
    left: 100px; top: 168px;
    width: 1000px; height: 550px;
    background: var(--card-bg);
    border: 2px solid var(--card-edge);
    border-radius: 26px;
    overflow: hidden;
    box-shadow: 0 18px 40px rgba(0,0,0,0.18);
  }
  .brand {
    position: absolute;
    left: 62px; top: 58px;
    display: flex; align-items: center; gap: 16px;
  }
  .brand-square {
    width: 58px; height: 58px;
    background: var(--brand-red);
  }
  .brand-name {
    font-weight: 800;
    font-size: 54px;
    color: var(--brand-red);
    letter-spacing: -0.5px;
    line-height: 1;
  }
  .info-band {
    position: absolute;
    left: 0; top: 239px;
    width: 100%; height: 214px;
    background: linear-gradient(90deg, var(--band-navy) 0%, var(--band-navy-deep) 100%);
  }
  .person-name {
    position: absolute;
    left: 58px; top: 14px;
    font-weight: 800;
    font-size: 38px;
    color: var(--brand-red);
    letter-spacing: 0.5px;
  }
  .person-title {
    position: absolute;
    left: 60px; top: 62px;
    font-size: 24px;
    color: var(--text-muted);
  }
  .contact-list {
    position: absolute;
    left: 58px; top: 108px;
    list-style: none;
  }
  .contact-list li {
    display: flex; align-items: center; gap: 6px;
    font-size: 26px;
    line-height: 32px;
    color: var(--text-light);
  }
  .contact-icon { width: 20px; height: 20px; flex: none; }
  .band-emblem {
    position: absolute;
    right: 58px; top: -6px;
    width: 214px; height: 214px;
    border-radius: 50%;
    background: var(--brand-red);
    border: 6px solid var(--card-bg);
  }
  .address {
    position: absolute;
    left: 56px; top: 468px;
    font-size: 26px;
    color: var(--text-dark);
  }
</style>
</head>
<body>
  <main class="business-card">
    <header class="brand">
      <span class="brand-square"></span>
      <span class="brand-name">Brindovalle.com</span>
    </header>

    <section class="info-band">
      <h1 class="person-name">MARCO FELDANI</h1>
      <p class="person-title">Director</p>
      <ul class="contact-list">
        <li>
          <svg class="contact-icon" viewBox="0 0 24 24" aria-hidden="true">
            <path fill="#e0161d" d="M6.6 10.8a15 15 0 0 0 6.6 6.6l2.2-2.2a1 1 0 0 1 1-.25 11.4 11.4 0 0 0 3.6.57 1 1 0 0 1 1 1V20a1 1 0 0 1-1 1A17 17 0 0 1 3 4a1 1 0 0 1 1-1h3.5a1 1 0 0 1 1 1c0 1.25.2 2.45.57 3.57a1 1 0 0 1-.25 1z"/>
          </svg>
          555-014-2287
        </li>
        <li>
          <svg class="contact-icon" viewBox="0 0 24 24" aria-hidden="true">
            <rect x="2" y="5" width="20" height="14" fill="#e0161d"/>
            <path d="M2 5l10 8 10-8" fill="none" stroke="#0e1640" stroke-width="1.6"/>
          </svg>
          info@brindovalle.com
        </li>
        <li>
          <svg class="contact-icon" viewBox="0 0 24 24" aria-hidden="true">
            <circle cx="12" cy="12" r="9" fill="#e0161d"/>
          </svg>
          brindovalle
        </li>
      </ul>
      <div class="band-emblem" aria-hidden="true"></div>
    </section>

    <p class="address">2240 W Larkin, Fairbrook, Oklahoma 74020</p>
  </main>
</body>
</html>
```